Fitness website

Website for a fitness brand (see attached specs). Design needs to be modern and vibrant with CTAs on every page. We will provide logos, images, etc but for now user placeholder text and images. For now use the name 'Corvane Athletics' as the name to use on the design. The goal of this site is to either get people to join the gym (5 physical locations across the US); buy an online program; buy merch or supplements or sign up for the newsletter. Pleas use images from this foldeR: https://filebarn.example/share/folders/8QwTz41mKpLrXv93NdYe7HsaBuJ0Cf2_R?usp=sharing

We will be coding this in ReactNative. Lots more work for the winner as well, this is a 1st project for us.

Target Market(s)

fitness enthusiats

Industry/Entity Type

fitness, health, wellness

Number of Pages Required

5+ page

Font styles to use
Other font styles liked:
• Lato

Colors
0054AA
0677BA
7BADD7
CADEEF
E8F1F8
0094D4
00A9DD
6FCCEA
C7EBF8
E9F6FB
00AB8E
00BBA5
67D7C9
C6EFE9
E9F9F6
EE7325
F08F49
F5BC92
FAE3D3
FDF4ED

Requirements
Must have
• must be reactive. most people will view it first on mobile
Nice to have
• video in hero section of top of home page

```html
<!DOCTYPE html>
<html lang="en">
<head>
<meta charset="utf-8">
<title>Corvane Athletics – Mobile Screens</title>
<link href="https://fonts.googleapis.com/css2?family=Josefin+Sans:ital,wght@0,300;0,400;0,600;0,700;1,300;1,400;1,600;1,700&family=Orbitron:wght@700;900&display=swap" rel="stylesheet">
<style>
:root{
  --page:#000;
  --screen:#1c3a3e;
  --header:#1b2f32;
  --teal:#00ab8e;
  --teal-bright:#00bba5;
  --teal-soft:#67d7c9;
  --ink:#e9f9f6;
  --muted:#c6efe9;
  --glass:rgba(30,90,88,.72);
  --pill:#12292c;
  --gray-box:#5a5d5e;
  --gray-track:#8c8f90;
  --gray-text:#b4b6b7;
  --stat-box:#284d53;
}
*{box-sizing:border-box;margin:0;padding:0}
html,body{width:1200px;height:1200px;overflow:hidden;background:var(--page)}
body{position:relative;font-family:"Josefin Sans",sans-serif;color:var(--ink)}
.screen{position:absolute;overflow:hidden;background:var(--screen)}
.screen *{position:absolute}
.h-ital{font-style:italic;font-weight:600;text-align:center;left:0;right:0;line-height:1.1}
.p-ital{font-style:italic;font-weight:300;text-align:center;line-height:1.4;color:var(--ink)}
.btn{background:var(--teal);color:#fff;border-radius:20px;display:flex;align-items:center;justify-content:center;font-style:italic;font-weight:400}
.pill{border:1px solid var(--teal);border-radius:10px;display:flex;align-items:center;justify-content:center;font-size:6.5px;font-style:italic;gap:3px;white-space:nowrap}
.dots{display:flex;gap:5px}
.dots span{position:static;width:4px;height:4px;border-radius:50%;background:#9db4b5}
.dots span.on{background:#fff}
.screen .carousel .dots{position:static}
.brand{display:flex;align-items:center;gap:5px;font-weight:600;font-size:8px;line-height:1;letter-spacing:.4px;text-transform:uppercase}
.brand i{position:static;width:11px;height:11px;background:var(--ink)}
.brand b{position:static;font-weight:600}
.hero-word{font-family:Orbitron,sans-serif;font-weight:900;color:transparent;-webkit-text-stroke:1.3px var(--teal-bright);letter-spacing:-.5px;white-space:nowrap}
/* location cards */
.glass{background:var(--glass);border:1px solid rgba(103,215,201,.45);border-radius:10px;box-shadow:0 0 10px rgba(0,187,165,.35)}
.glass .lbl{left:18px;top:13px;font-size:7px;font-style:italic;white-space:nowrap}
.glass .city{left:18px;top:27px;font-size:13px;font-style:italic;letter-spacing:.3px;white-space:nowrap}
.glass .desc{left:18px;right:8px;font-size:7px;font-style:italic;line-height:1.45}
.glass .addr{left:40px;right:6px;font-size:5px;line-height:1.3}
.glass .pin{left:18px;width:13px;height:17px}
.glass .map{left:18px;width:84px;height:18px;background:var(--pill);border-radius:10px;font-size:7.5px;font-style:italic;display:flex;align-items:center;justify-content:center}
.glass .badge{right:-2px;top:-2px;width:24px;height:24px;border-radius:50%;background:rgba(0,187,165,.35);border:1px solid rgba(103,215,201,.5)}
/* menu */
.menu a{font-size:7px;color:var(--ink);text-decoration:none;left:44px;white-space:nowrap}
.menu .ico{left:33px;width:7px;height:7px;border:1px solid var(--ink);border-radius:2px}
.stat-title{position:absolute;left:896px;width:250px;font-size:12.5px;letter-spacing:.2px;text-align:center;white-space:nowrap;line-height:1}
.stat-box{position:absolute;left:896px;width:250px;height:37px;background:var(--stat-box)}
.stat-track{position:absolute;left:8px;right:8px;top:9px;height:19px;border-radius:10px;background:#2f5e63}
.stat-fill{position:absolute;left:0;top:0;bottom:0;border-radius:10px;background:var(--teal)}
.stat-num{position:absolute;left:0;right:0;top:0;bottom:0;display:flex;align-items:center;justify-content:center;font-size:16px;color:#fff}
</style>
</head>
<body>

<!-- SCREEN 1: Home -->
<section class="screen" style="left:60px;top:17px;width:250px;height:1165px;border-radius:20px 20px 0 0;">
  <div role="img" aria-label="Hero photo of an athlete training with a cable machine" style="left:0;top:0;width:250px;height:460px;background:linear-gradient(160deg,#3d5a5d 0%,#2a4548 45%,#1f3a3d 100%)"></div>
  <header style="left:0;top:0;width:250px;height:58px;background:var(--header)">
    <div class="brand" style="left:18px;top:23px"><i></i><b>Corvane<br>Athletics</b></div>
    <svg style="right:19px;top:22px" width="22" height="16" viewBox="0 0 22 16"><g stroke="#e9f9f6" stroke-width="1.5"><line x1="4" y1="1" x2="22" y2="1"/><line x1="0" y1="8" x2="22" y2="8"/><line x1="6" y1="15" x2="22" y2="15"/></g></svg>
  </header>
  <div class="hero-word" style="left:12px;top:154px;font-size:40px">UNLEASH</div>
  <div style="left:30px;top:200px;font-style:italic;font-weight:600;font-size:22px;color:transparent;-webkit-text-stroke:.8px #d8e6e6">Your</div>
  <div class="hero-word" style="left:74px;top:190px;font-size:40px">POWER</div>
  <p class="p-ital" style="left:18px;width:214px;top:244px;font-size:10.5px">Join our community of athletes and achievers In gym or online. Your transfor-mation starts here</p>
  <div class="btn" style="left:71px;top:332px;width:109px;height:31px;font-size:10.5px">Start Now</div>
  <div class="pill" style="left:89px;top:386px;width:72px;height:16px">Gym near me <span style="position:static;width:6px;height:6px;border:1px solid #fff;border-radius:50%"></span></div>
  <div class="dots" style="left:111px;top:435px"><span></span><span class="on"></span><span></span></div>

  <div style="left:0;top:460px;width:250px;height:705px;background:var(--screen)"></div>
  <h2 class="h-ital" style="top:486px;font-size:21px">Choose Your Path</h2>
  <p class="p-ital" style="left:16px;width:218px;top:520px;font-size:10.5px">Train with expert-led programs designed for every goal, strength, endurance, or transfor-mation</p>
  <div role="img" aria-label="Program photo of a man curling a dumbbell in the gym" style="left:21px;top:584px;width:210px;height:267px;border-radius:14px;background:linear-gradient(180deg,#4a6c6a 0%,#2d5c57 50%,#1d4a45 100%)"></div>
  <div style="left:31px;top:703px;font-size:24px;font-style:italic;font-weight:400;letter-spacing:.4px;white-space:nowrap">Strength Builder</div>
  <p style="left:38px;width:150px;top:739px;font-size:9.5px;font-style:italic;font-weight:300;line-height:1.45">Focus on lifting heavier, buil-ding lean muscle, and maste-ring proper form.</p>
  <div class="dots" style="left:50px;top:818px"><span></span><span class="on"></span><span></span></div>
  <div class="btn" style="left:101px;top:803px;width:109px;height:31px;font-size:10px">Explore Programs</div>

  <div role="img" aria-label="Photo of a busy gym floor with members training" style="left:0;top:860px;width:250px;height:305px;background:linear-gradient(180deg,var(--screen) 0%,#2a4245 40%,#1e3538 100%)"></div>
  <h2 class="h-ital" style="top:908px;font-size:21px">Train Near You</h2>
  <p class="p-ital" style="left:20px;width:210px;top:944px;font-size:10px">Your training circle is never far away.<br>5 locations across the US.</p>
  <svg style="left:60px;top:998px" width="130" height="130" viewBox="0 0 130 130">
    <circle cx="65" cy="65" r="58" fill="none" stroke="rgba(0,171,142,.35)" stroke-width="8"/>
    <path d="M65 7 A58 58 0 1 1 12 88" fill="none" stroke="#00ab8e" stroke-width="8"/>
    <circle cx="65" cy="65" r="34" fill="#00ab8e"/>
    <circle cx="65" cy="65" r="23" fill="none" stroke="#fff" stroke-width="2.5"/>
    <g stroke="#fff" stroke-width="2.5" stroke-linecap="round"><line x1="65" y1="65" x2="65" y2="51"/><line x1="65" y1="65" x2="54" y2="61"/></g>
    <circle cx="65" cy="65" r="3" fill="#fff"/>
  </svg>
</section>

<!-- SCREEN 2: Locations -->
<section class="screen" style="left:338px;top:17px;width:251px;height:1165px;background:#1d3c40">
  <div role="img" aria-label="Photo of a woman training with a barbell" style="left:23px;top:18px;width:176px;height:205px;border-radius:12px;background:linear-gradient(160deg,#5c6660,#3a4a48 55%,#2a3a3a)"></div>
  <div class="glass" style="left:4px;top:108px;width:44px;height:52px;border-radius:8px;box-shadow:none"></div>
  <div class="glass" style="left:117px;top:43px;width:120px;height:154px">
    <div class="badge"></div><div class="lbl">Corvane Athletics</div><div class="city">Los Angeles,CA</div>
    <div class="desc" style="top:52px">Experience top-tier fit-ness in sunny LA</div>
    <svg class="pin" style="top:82px" viewBox="0 0 13 17"><path d="M6.5 0A6.5 6.5 0 0 0 0 6.5C0 11 6.5 17 6.5 17S13 11 13 6.5A6.5 6.5 0 0 0 6.5 0z" fill="#00bba5"/><circle cx="6.5" cy="6.5" r="2.5" fill="#1d3c40"/></svg>
    <div class="addr" style="top:85px">418 Granite Ave, Los Angeles, CA 90012</div>
    <div class="map" style="top:119px">See on Map</div>
  </div>

  <div role="img" aria-label="Photo of a man lifting with a group training behind" style="left:51px;top:249px;width:180px;height:206px;border-radius:12px;background:linear-gradient(160deg,#4a5552,#38453f 50%,#25302f)"></div>
  <div class="glass" style="left:20px;top:283px;width:120px;height:138px">
    <div class="badge"></div><div class="lbl">Corvane Athletics</div><div class="city">Miami, FL</div>
    <div class="desc" style="top:52px">Dive into your fitness goals in vibrant Miami.</div>
    <svg class="pin" style="top:82px" viewBox="0 0 13 17"><path d="M6.5 0A6.5 6.5 0 0 0 0 6.5C0 11 6.5 17 6.5 17S13 11 13 6.5A6.5 6.5 0 0 0 6.5 0z" fill="#00bba5"/><circle cx="6.5" cy="6.5" r="2.5" fill="#1d3c40"/></svg>
    <div class="addr" style="top:85px">72 Harbor Row, Miami, FL 33130</div>
    <div class="map" style="top:110px">See on Map</div>
  </div>

  <div role="img" aria-label="Photo of a woman pressing a loaded barbell overhead" style="left:20px;top:480px;width:179px;height:206px;border-radius:12px;background:linear-gradient(160deg,#3a4f63,#4a5a60 50%,#2d3a3d)"></div>
  <div class="glass" style="left:110px;top:511px;width:121px;height:144px">
    <div class="badge"></div><div class="lbl">Corvane Athletics</div><div class="city">Chicago, IL</div>
    <div class="desc" style="top:52px">Get fit in the Windy City with our expert trainers</div>
    <svg class="pin" style="top:90px" viewBox="0 0 13 17"><path d="M6.5 0A6.5 6.5 0 0 0 0 6.5C0 11 6.5 17 6.5 17S13 11 13 6.5A6.5 6.5 0 0 0 6.5 0z" fill="#00bba5"/><circle cx="6.5" cy="6.5" r="2.5" fill="#1d3c40"/></svg>
    <div class="addr" style="top:93px">905 Lakeview Dr, Chicago, IL 60614</div>
    <div class="map" style="top:117px">See on Map</div>
  </div>

  <div role="img" aria-label="Photo of athletes training with kettlebells" style="left:51px;top:710px;width:178px;height:206px;border-radius:12px;background:linear-gradient(160deg,#4c5552,#39434a 50%,#262f33)"></div>
  <div class="glass" style="left:20px;top:744px;width:120px;height:138px">
    <div class="badge"></div><div class="lbl">Corvane Athletics</div><div class="city">Dallas, TX</div>
    <div class="desc" style="top:52px">Achieve your best self in the heart of Texas.</div>
    <svg class="pin" style="top:82px" viewBox="0 0 13 17"><path d="M6.5 0A6.5 6.5 0 0 0 0 6.5C0 11 6.5 17 6.5 17S13 11 13 6.5A6.5 6.5 0 0 0 6.5 0z" fill="#00bba5"/><circle cx="6.5" cy="6.5" r="2.5" fill="#1d3c40"/></svg>
    <div class="addr" style="top:85px">231 Ember St, Dallas, TX 75204</div>
    <div class="map" style="top:110px">See on Map</div>
  </div>

  <div role="img" aria-label="Photo of a group class doing squats in a gym" style="left:24px;top:938px;width:176px;height:204px;border-radius:12px;background:linear-gradient(160deg,#44504c,#3a443c 50%,#2a3330)"></div>
  <div class="glass" style="left:111px;top:969px;width:120px;height:152px">
    <div class="badge"></div><div class="lbl">Corvane Athletics</div><div class="city">New York, NY</div>
    <div class="desc" style="top:52px">Join our vibrant com-munity in the heart of NYC and elevate your fitness journey</div>
    <svg class="pin" style="top:98px" viewBox="0 0 13 17"><path d="M6.5 0A6.5 6.5 0 0 0 0 6.5C0 11 6.5 17 6.5 17S13 11 13 6.5A6.5 6.5 0 0 0 6.5 0z" fill="#00bba5"/><circle cx="6.5" cy="6.5" r="2.5" fill="#1d3c40"/></svg>
    <div class="addr" style="top:101px">66 Forge Pl, New York, NY 10013</div>
    <div class="map" style="top:125px">See on Map</div>
  </div>
</section>

<!-- SCREEN 3: Shop, about, reviews, newsletter -->
<section class="screen" style="left:617px;top:17px;width:250px;height:1165px;background:#1e3b3f">
  <h2 class="h-ital" style="top:14px;font-size:21px">Fuel Your<br>Performance</h2>
  <p class="p-ital" style="left:18px;width:214px;top:72px;font-size:9.5px">Discover premium Corvane apparel and performance supplements.</p>
  <div style="left:15px;top:112px;width:218px;height:144px;border-radius:10px;background:#22474a;overflow:hidden">
    <div role="img" aria-label="Product photo of a water bottle, yoga mat and wrist wraps" style="left:0;top:0;width:116px;height:144px;background:linear-gradient(150deg,#c9e06b,#b9dd47 50%,#dfe7d8)"></div>
    <div style="left:122px;top:10px;font-size:17px;font-style:italic;font-weight:600;white-space:nowrap">Gear Up</div>
    <p style="left:118px;right:8px;top:34px;font-size:6.8px;font-style:italic;text-align:right;line-height:1.45">Discover high-quality apparel and performan-ce supplements desig-ned to keep you moving, recovering, and perfor-ming at your best</p>
    <div class="btn" style="left:130px;top:108px;width:78px;height:19px;font-size:9.5px">Shop Now</div>
  </div>
  <div class="dots" style="left:100px;top:280px"><span></span><span class="on"></span><span></span></div>
  <div class="pill" style="left:147px;top:274px;width:61px;height:14px">View more →</div>

  <div role="img" aria-label="Photo of gym benches in a dim training room" style="left:0;top:310px;width:250px;height:480px;background:linear-gradient(180deg,#1e3b3f 0%,#2a4346 40%,#22393c 100%)"></div>
  <h2 style="left:18px;top:322px;font-size:21px;font-style:italic;font-weight:600;white-space:nowrap">About us ▾</h2>
  <div style="left:15px;right:13px;top:346px;height:1px;background:rgba(103,215,201,.4)"></div>
  <p class="p-ital" style="left:15px;width:222px;top:357px;font-size:7.5px;font-weight:400">At Corvane Athletics, we believe strength is more than phy-sical it's a mindset. Our mission is to empower every athle-te to push beyond limits, whether in the gym or online. With expert coaches, proven programs, and a passionate community, we're here to help you train harder, recover smarter, and become unstoppable.</p>
  <div class="pill" style="left:147px;top:428px;width:61px;height:14px">Learn more →</div>

  <h2 class="h-ital" style="top:467px;font-size:21px">Real People. Real<br>Results</h2>
  <p class="p-ital" style="left:18px;width:214px;top:518px;font-size:9.5px">Thousands of members transformed their lives with Corvane Athletics.</p>

  <div class="glass" style="left:7px;top:629px;width:58px;height:127px;background:rgba(30,70,70,.6);box-shadow:none;overflow:hidden">
    <p style="left:6px;right:2px;top:60px;font-size:5px;font-style:italic;line-height:1.8;text-align:center">"Corvane changed my life. The programs are tough and perfect. I never felt so"</p>
  </div>
  <div class="glass" style="left:187px;top:629px;width:56px;height:127px;background:rgba(30,70,70,.6);box-shadow:none;overflow:hidden">
    <p style="left:2px;right:6px;top:60px;font-size:5px;font-style:italic;line-height:1.8;text-align:center">back in shape, a lifestyle. people, and the relatable."</p>
  </div>
  <div class="glass" style="left:51px;top:604px;width:148px;height:173px;background:#1f4548">
    <div class="h-ital" style="top:47px;font-size:12px;font-weight:400">Tessa R.</div>
    <div class="h-ital" style="top:64px;font-size:7px;font-weight:300">Los Angeles, CA</div>
    <p class="p-ital" style="left:12px;width:124px;top:92px;font-size:7.5px;line-height:1.85;font-weight:400">"The community vibe is amazing! Whether you train online or in person, you always feel suppor-ted. The trainers really push you to reach your full potential."</p>
  </div>
  <div role="img" aria-label="Member portrait" style="left:88px;top:568px;width:75px;height:75px;border-radius:50%;background:radial-gradient(circle at 50% 40%,#e8ddd0,#c9a27a 60%,#f3efe9 61%)"></div>

  <div class="carousel" style="left:58px;top:795px;display:flex;align-items:center;gap:6px">
    <span style="position:static;width:12px;height:12px;border:1px solid var(--teal-soft);border-radius:50%"></span>
    <div class="dots"><span></span><span></span><span></span><span></span><span></span><span></span><span></span><span class="on"></span><span></span></div>
    <span style="position:static;width:12px;height:12px;border:1px solid var(--teal-soft);border-radius:50%"></span>
  </div>

  <div style="left:0;top:810px;width:250px;height:355px;background:#1f4044"></div>
  <h2 class="h-ital" style="top:832px;font-size:21px">Stay in the Zone</h2>
  <p class="p-ital" style="left:16px;width:218px;top:862px;font-size:7.8px;font-weight:400">Join our community to get exclusive training tips, special offers, and the latest updates from Corvane Athletics straight to your inbox.</p>
  <div style="left:19px;top:907px;width:209px;height:34px;border-radius:17px;background:var(--ink);color:#8fb3b0;display:flex;align-items:center;justify-content:center;font-size:11px;font-style:italic">Your email</div>
  <div class="btn" style="left:19px;top:954px;width:209px;height:33px;font-size:11px">Suscribe</div>
  <svg style="left:228px;top:1004px" width="14" height="8" viewBox="0 0 14 8"><path d="M1 7 7 1l6 6" fill="none" stroke="#c6efe9" stroke-width="1.2"/></svg>
  <nav style="left:0;top:1029px;width:250px;height:30px;font-size:9px;font-style:italic;color:var(--muted);white-space:nowrap">
    <span style="left:33px;top:0;text-decoration:underline">Home</span>
    <span style="left:82px;top:0">Programs</span>
    <span style="left:158px;top:0">Shop</span>
    <span style="left:194px;top:0">About</span>
    <span style="left:44px;top:15px">Blog</span>
    <span style="left:94px;top:15px">Gym location</span>
    <span style="left:163px;top:15px">Ressources</span>
  </nav>
  <div class="brand" style="left:80px;top:1079px;font-size:10px;color:#c6d8d8"><i style="width:16px;height:16px;background:#c6d8d8"></i><b>Corvane<br>Athletics</b></div>
  <div class="h-ital" style="top:1112px;font-size:12px;font-weight:300;color:#4f8c86">Strength in Every Move !</div>
  <div class="h-ital" style="top:1137px;font-size:4.5px;font-weight:400">© 2025 Corvane Athletics. All rights reserved.</div>
  <div class="h-ital" style="top:1148px;font-size:4.5px;font-weight:400">Terms of Service | Privacy Policy</div>
</section>

<!-- SCREEN 4: Open menu -->
<section class="screen" style="left:896px;top:17px;width:250px;height:460px;border-radius:20px 20px 0 0">
  <div role="img" aria-label="Hero photo of an athlete training with a cable machine" style="left:0;top:0;width:250px;height:460px;background:linear-gradient(160deg,#3d5a5d 0%,#2a4548 45%,#1f3a3d 100%)"></div>
  <header style="left:0;top:0;width:250px;height:58px;background:var(--header)">
    <div class="brand" style="left:18px;top:23px"><i></i><b>Corvane<br>Athletics</b></div>
  </header>
  <div class="hero-word" style="left:12px;top:154px;font-size:40px">UNLEASH</div>
  <div style="left:30px;top:200px;font-style:italic;font-weight:600;font-size:22px;color:transparent;-webkit-text-stroke:.8px #d8e6e6">Your</div>
  <p class="p-ital" style="left:18px;width:214px;top:244px;font-size:10.5px">Join our community of athletes and achievers In gym or online.</p>
  <div class="dots" style="left:111px;top:435px"><span></span><span class="on"></span><span></span></div>

  <div class="menu" style="left:71px;top:23px;width:179px;height:371px;background:#1d4246">
    <svg style="left:147px;top:8px" width="12" height="12" viewBox="0 0 12 12"><g stroke="#fff" stroke-width="1.5"><line x1="1" y1="1" x2="11" y2="11"/><line x1="11" y1="1" x2="1" y2="11"/></g></svg>
    <div role="img" aria-label="User profile portrait" style="left:27px;top:10px;width:80px;height:80px;border-radius:50%;background:radial-gradient(circle at 50% 45%,#d9b89a,#8a6a4f 55%,#f4f4f2 57%)"></div>
    <svg style="left:113px;top:40px" width="18" height="18" viewBox="0 0 18 18"><path d="M4 13V8a5 5 0 0 1 10 0v5l1.5 1.5h-13z" fill="none" stroke="#e9f9f6" stroke-width="1"/><circle cx="14" cy="4" r="3.5" fill="#e3262d"/><text x="14" y="6" font-size="5" fill="#fff" text-anchor="middle" font-family="Josefin Sans,sans-serif">7</text></svg>
    <div style="left:28px;top:100px;font-size:11px;font-style:italic;font-weight:600;white-space:nowrap">Marlo Quinn</div>
    <div style="left:32px;top:118px;font-size:7px;white-space:nowrap">⌖ Los Angeles CA</div>
    <div style="left:16px;right:16px;top:132px;height:1px;background:rgba(103,215,201,.35)"></div>
    <span class="ico" style="top:147px"></span><a style="top:147px">Home</a>
    <span class="ico" style="top:161px;border-radius:50%"></span><a style="top:161px">Programs</a>
    <a style="top:175px">About</a>
    <a style="top:186px">Gym near me</a>
    <a style="top:197px">Ressources</a>
    <a style="top:207px">Contact us</a>
    <div style="left:16px;right:16px;top:222px;height:1px;background:rgba(103,215,201,.35)"></div>
    <span class="ico" style="top:236px"></span><a style="top:236px">Shop →</a>
    <span class="ico" style="top:257px"></span><a style="top:257px">Workout History</a>
    <span class="ico" style="top:270px;border-radius:50%"></span><a style="top:270px">My progress</a>
    <span class="ico" style="top:281px;border:none;border-bottom:1px solid #e9f9f6"></span><a style="top:281px">Edit Profile</a>
    <span class="ico" style="top:292px;border-radius:50%"></span><a style="top:292px">Account Settings</a>
    <div style="left:16px;right:16px;top:306px;height:1px;background:rgba(103,215,201,.35)"></div>
    <div style="left:2px;top:308px;width:108px;height:30px;border-radius:15px;background:#00695a;filter:blur(3px)"></div>
    <div style="left:44px;top:316px;width:20px;height:8px;border-radius:4px;background:#12292c"></div>
    <div style="left:56px;top:315px;width:9px;height:9px;border-radius:50%;background:#fff"></div>
    <a style="top:345px">Log Out</a>
  </div>
</section>

<!-- Progress stats -->
<div class="stat-title" style="top:564px;color:var(--teal-bright)">MOBILE VERSION/ WORK PROGRESS</div>
<div class="stat-box" style="top:582px"><div class="stat-track"><div class="stat-fill" style="width:81%"></div><div class="stat-num">79%</div></div></div>

<div class="stat-title" style="top:656px;color:var(--teal-bright)">DESKTOP VERSION/ WORK PROGRESS</div>
<div class="stat-box" style="top:674px"><div class="stat-track"><div class="stat-fill" style="width:12%"></div><div class="stat-num">7%</div></div></div>

<div class="stat-title" style="top:769px;color:var(--gray-text);font-size:18px">MOBILE USERS</div>
<div class="stat-box" style="top:795px;background:var(--gray-box)"><div class="stat-track" style="background:#6f7273"><div class="stat-fill" style="width:81%;background:var(--gray-track)"></div><div class="stat-num">79%</div></div></div>

<div class="stat-title" style="top:861px;color:var(--gray-text);font-size:18px">DESKTOP USERS</div>
<div class="stat-box" style="top:887px;background:var(--gray-box)"><div class="stat-track" style="background:#6f7273"><div class="stat-fill" style="width:25%;background:var(--gray-track)"></div><div class="stat-num">21%</div></div></div>

</body>
</html>
```